Simple Logo Design for Semi-Clear Plastic Frosted Card stock

Create a business card on frosted plastic. compliment existing logo elements with a tree trunk, roots, or seed at the lower half and the full logo both on the front.

Contact information will go on a solid portion of the back of this design since this card stock is semi-transparent.

It is important to consider this plastic card stock medium in your design. I found helpful tips and guides listed at vellaprint-sample.net: be careful to understand ink printed on plastic cards cannot have too much of a consistent print area or risks peeling and fine lines can easily scratch off.
Updates

2" x 3.5" 20PT Clear Plastic Business cards with Round corners Please get info or templates here: https://www.vellaprint-sample.net/product-detail/2-x-35-20pt-clear-plastic-business-cards-with-round-corners

Target Market(s)

Not for profit- religion

Industry/Entity Type

Business

Must include complementary elements to the existing logo

Font styles to use
Decorative

Colors
000000

Requirements
Must have
• Elements of community, nature and oneness. Such as: seed, roots, tree trunk, etc.
• Three lines of space on the back for Name, Title, Phone Number.
Nice to have
• I like a light use of decorative elements
Should not have
• No eyes, from faces or animals.

```html
<!DOCTYPE html>
<html lang="en">
<head>
<meta charset="utf-8">
<title>Evergrove Path – Business Card</title>
<link href="https://fonts.googleapis.com/css2?family=Arimo:wght@400;700&display=swap" rel="stylesheet">
<style>
  :root {
    --backdrop: #c3cbcb;
    --frost: #eef2f1;
    --frost-edge: #dfe6e4;
    --teal: #26756e;
    --teal-deep: #1f665f;
    --leaf: #4ea24a;
    --leaf-bright: #5bb04f;
    --ink-light: #ffffff;
  }
  html, body {
    margin: 0;
    width: 1200px;
    height: 1034px;
    overflow: hidden;
    background: var(--backdrop);
  }
  .card {
    position: absolute;
    left: 100px;
    top: 222px;
    width: 1000px;
    height: 590px;
    display: block;
  }
  .card text { font-family: "Arimo", Arial, sans-serif; }
  .holder-name { font-weight: 700; font-size: 45px; fill: var(--ink-light); }
  .holder-title { font-weight: 400; font-size: 31px; fill: var(--ink-light); }
  .holder-phone { font-weight: 400; font-size: 34px; fill: var(--ink-light); }
  .brand-name { font-weight: 400; font-size: 44px; letter-spacing: 2px; fill: var(--teal); }
</style>
</head>
<body>
  <svg class="card" viewBox="0 0 1000 590" xmlns="http://www.w3.org/2000/svg">
    <defs>
      <clipPath id="card-shape">
        <rect x="0" y="0" width="1000" height="590" rx="34" ry="34"/>
      </clipPath>
      <linearGradient id="frost-fill" x1="0" y1="0" x2="1" y2="1">
        <stop offset="0" stop-color="var(--frost)"/>
        <stop offset="1" stop-color="var(--frost-edge)"/>
      </linearGradient>
    </defs>

    <g clip-path="url(#card-shape)">
      <!-- frosted base -->
      <rect class="frost-panel" width="1000" height="590" fill="url(#frost-fill)"/>

      <!-- upper teal band with leaf accent edge -->
      <polygon class="accent-stripe" points="323,0 340,0 556,293 539,293" fill="var(--leaf-bright)"/>
      <polygon class="teal-band" points="340,0 1000,0 1000,293 556,293" fill="var(--teal)"/>

      <!-- lower green band with teal accent edge -->
      <polygon class="accent-stripe-lower" points="539,293 556,293 340,590 323,590" fill="var(--teal-deep)"/>
      <polygon class="leaf-band" points="556,293 1000,293 1000,590 340,590" fill="var(--leaf)"/>
    </g>

    <!-- brand mark -->
    <circle class="brand-dot" cx="195" cy="235" r="34" fill="var(--teal)"/>
    <text class="brand-name" x="24" y="340">EVERGROVE PATH</text>

    <!-- holder details -->
    <text class="holder-name" x="963" y="155" text-anchor="end">Arun Dev Mitra</text>
    <text class="holder-title" x="963" y="202" text-anchor="end">Chief Executive Officer</text>
    <text class="holder-phone" x="963" y="445" text-anchor="end">555-318-0472</text>
  </svg>
</body>
</html>
```